New Bicycle shop business card

Hi!
I'm looking for a business card for my new proffesional bike mechanics shop. This shop is only for fixing broken bikes and not selling bikes.
Peferbly a modern and sleek and modern design.
Colors: black, grey, red, white
Information:
Name: Rijwielwerkplaats Vanhoutte
Shop owner: Bart Vanhoutte & Marieke Segers
Website: www.rijwielwerkplaats-vanhoutte.be
Email: info@rijwielwerkplaats-vanhoutte.be
Phone number: +32471902368
Street adres: Kerkweg 46
9940 Bellebeke
Slogan/shop information: Herstellingen van alle merken.
Logo: see files.
Target Market(s)
People who seek a mechanic to fix or upgrade their bikes.
Contact Information for Business Card
Information:
Website: info@rijwielwerkplaats-vanhoutte.be
9940 Bellebeke
Logo: see files.

```html
<!DOCTYPE html>
<html lang="nl">
<head>
<meta charset="utf-8">
<title>Rijwielwerkplaats Vanhoutte – visitekaart</title>
<link href="https://fonts.googleapis.com/css2?family=Josefin+Sans:wght@600&family=Roboto:wght@400;700&display=swap" rel="stylesheet">
<style>
  :root {
    --page: #dcd8d4;
    --card: #f4f2ef;
    --ink: #1e1c1c;
    --red: #d52a3a;
    --white: #ffffff;
    --soft-pink: #f6c9ce;
  }
  * { box-sizing: border-box; margin: 0; padding: 0; }
  html, body {
    width: 1200px;
    height: 1054px;
    overflow: hidden;
    background: var(--page);
  }
  .business-card {
    position: absolute;
    left: 100px;
    top: 227px;
    width: 1000px;
    height: 600px;
    background: var(--card);
    box-shadow: 0 10px 30px rgba(0,0,0,0.12);
    font-family: "Roboto", Arial, sans-serif;
    color: var(--ink);
  }
  .brand-name {
    position: absolute;
    left: 61px;
    top: 52px;
    font-family: "Roboto", Arial, sans-serif;
    font-weight: 700;
    font-size: 40px;
    line-height: 46px;
    letter-spacing: 1px;
    color: var(--ink);
    text-transform: uppercase;
  }
  .contact-band {
    position: absolute;
    left: 0;
    top: 225px;
    width: 100%;
    height: 300px;
    background: var(--red);
  }
  .person-name {
    position: absolute;
    left: 61px;
    top: 24px;
    font-family: "Josefin Sans", Arial, sans-serif;
    font-weight: 600;
    font-size: 36px;
    letter-spacing: 1px;
    color: var(--white);
    text-transform: uppercase;
  }
  .person-role {
    position: absolute;
    left: 61px;
    top: 70px;
    font-size: 23px;
    color: var(--white);
  }
  .contact-list {
    position: absolute;
    left: 61px;
    top: 122px;
    list-style: none;
  }
  .contact-list li {
    display: flex;
    align-items: center;
    height: 37px;
    font-size: 25px;
    color: var(--white);
  }
  .contact-list svg {
    width: 22px;
    height: 22px;
    margin-right: 28px;
    fill: var(--soft-pink);
  }
  .address {
    position: absolute;
    left: 61px;
    top: 243px;
    font-size: 23px;
    color: var(--soft-pink);
  }
  .tagline {
    position: absolute;
    left: 61px;
    top: 548px;
    font-size: 23px;
    color: var(--ink);
  }
</style>
</head>
<body>
  <div class="business-card">
    <div class="brand-name">Rijwielwerkplaats<br>Vanhoutte</div>

    <section class="contact-band">
      <div class="person-name">Marieke Segers</div>
      <div class="person-role">Owner</div>
      <ul class="contact-list">
        <li>
          <svg viewBox="0 0 24 24" aria-hidden="true"><path d="M6.6 10.8a15.1 15.1 0 0 0 6.6 6.6l2.2-2.2a1 1 0 0 1 1-.25 11.4 11.4 0 0 0 3.6.57 1 1 0 0 1 1 1V20a1 1 0 0 1-1 1A17 17 0 0 1 3 4a1 1 0 0 1 1-1h3.5a1 1 0 0 1 1 1 11.4 11.4 0 0 0 .57 3.6 1 1 0 0 1-.25 1z"/></svg>
          +32471902368
        </li>
        <li>
          <svg viewBox="0 0 24 24" aria-hidden="true"><path d="M2 5h20v14H2z M4 7v.4l8 5.2 8-5.2V7z" fill-rule="evenodd"/></svg>
          www.rijwielwerkplaats-vanhoutte.be
        </li>
        <li>
          <svg viewBox="0 0 24 24" aria-hidden="true"><path d="M12 2a10 10 0 1 0 0 20 10 10 0 0 0 0-20zm6.9 6h-2.9a15.7 15.7 0 0 0-1.4-3.6A8 8 0 0 1 18.9 8zM12 4a14 14 0 0 1 1.9 4h-3.8A14 14 0 0 1 12 4zM4.3 14a8 8 0 0 1 0-4h3.4a16.5 16.5 0 0 0 0 4zm.8 2H8a15.7 15.7 0 0 0 1.4 3.6A8 8 0 0 1 5.1 16zM8 8H5.1a8 8 0 0 1 4.3-3.6A15.7 15.7 0 0 0 8 8zm4 12a14 14 0 0 1-1.9-4h3.8A14 14 0 0 1 12 20zm2.3-6H9.7a14.7 14.7 0 0 1 0-4h4.6a14.7 14.7 0 0 1 0 4zm.3 5.6A15.7 15.7 0 0 0 16 16h2.9a8 8 0 0 1-4.3 3.6zM16.3 14a16.5 16.5 0 0 0 0-4h3.4a8 8 0 0 1 0 4z"/></svg>
          info@rijwielwerkplaats-vanhoutte.be
        </li>
      </ul>
      <div class="address">Kerkweg 46 9940 Bellebeke</div>
    </section>

    <div class="tagline">Herstellingen van alle merken</div>
  </div>
</body>
</html>
```